Fresh, modern, fun business card for pediatric dental practice

Need a business card for fresh, modern, fun pediatric dental practice

Clean look that matches our website's font and colors

We prefer the look of curved corners on business cards

Target Market(s)

parents (mothers) of young children, professionals, mid-high class

Industry/Entity Type

Dental

Contact Information for Business Card

Maplebrook Pediatric Dentistry
482 Quarry Lane
Suite 517
Ashgrove, PA 17590
717.555.0193
www.maplebrookkidsdental.example

Mei-Ran Tsai, DMD
Corinne Walbeck, DMD
(we are working on our email address, but we would like that on the card as well)

Font styles to use
Sans Serif

Requirements
Must have
• All info; we would also like to make cards for individual staff members
• colors from our website and color palatte, attatched
• use same font and design as website for branding
Nice to have
• clean, simple card that has a pop of color
• we would like to see a few designs with our tag line "where smiles get brighter"
• we are not sure if we want to have it on there or not
• we would like to see a few designs incorporating the ribbon graphic on our website where the word WELCOME is

```html
<!DOCTYPE html>
<html lang="en">
<head>
<meta charset="utf-8">
<title>Maplebrook Pediatric Dentistry — Business Card</title>
<link rel="stylesheet" href="https://fonts.googleapis.com/css2?family=Open+Sans:wght@400;700&family=Montserrat:wght@400;700&display=swap">
<style>
  :root {
    --stage: #1e1e1e;
    --card-dark: #121212;
    --card-light: #ffffff;
    --sun: #fbb416;
    --sun-faint: #3a2e12;
    --ink: #3a3a3a;
  }
  * { margin: 0; padding: 0; box-sizing: border-box; }
  html, body { width: 1200px; height: 852px; overflow: hidden; }
  body {
    background: var(--stage);
    display: flex;
    align-items: center;
    justify-content: center;
    gap: 40px;
    font-family: "Montserrat", sans-serif;
  }
  .card {
    position: relative;
    width: 520px;
    height: 300px;
    border-radius: 22px;
    overflow: hidden;
  }
  .card--back { background: var(--card-dark); }
  .card--front { background: var(--card-light); }

  .brand-name {
    font-family: "Open Sans", sans-serif;
    font-weight: 700;
    color: var(--sun);
    line-height: 1.05;
    letter-spacing: 0.5px;
  }
  .brand-name small { display: block; }

  .card--back .brand {
    position: absolute;
    left: 40px;
    bottom: 44px;
    display: flex;
    align-items: center;
    gap: 12px;
  }
  .card--back .brand-name { font-size: 30px; }
  .card--back .brand-name small { font-size: 17px; }
  .brand-dot {
    width: 34px; height: 34px; border-radius: 50%;
    background: var(--sun);
    flex: none;
  }
  .back-circle { position: absolute; right: 60px; top: 36px; }

  .card--front .brand { position: absolute; left: 34px; top: 34px; }
  .card--front .brand-name { font-size: 32px; }
  .card--front .brand-name small { font-size: 18px; }
  .front-circle { position: absolute; right: 36px; top: 40px; }

  .person { position: absolute; left: 34px; top: 126px; }
  .person-name {
    font-weight: 700;
    font-size: 18px;
    color: var(--sun);
    letter-spacing: 0.5px;
    text-transform: uppercase;
  }
  .person-title { font-size: 12px; color: var(--ink); margin-top: 2px; }
  .address { font-size: 12px; color: var(--ink); line-height: 1.4; margin-top: 6px; }
  .contact-list { list-style: none; margin-top: 6px; }
  .contact-list li {
    display: flex; align-items: center; gap: 8px;
    font-size: 12px; color: var(--ink); line-height: 1.5;
  }
  .contact-list svg { width: 10px; height: 10px; flex: none; }
</style>
</head>
<body>

  <section class="card card--back" aria-label="Card back">
    <svg class="back-circle" width="190" height="190" viewBox="0 0 190 190" aria-hidden="true">
      <circle cx="95" cy="95" r="80" fill="none" stroke="var(--sun-faint)" stroke-width="8"/>
    </svg>
    <div class="brand">
      <span class="brand-dot" aria-hidden="true"></span>
      <p class="brand-name">maplebrook<small>pediatric dentistry</small></p>
    </div>
  </section>

  <section class="card card--front" aria-label="Card front">
    <svg class="front-circle" width="150" height="150" viewBox="0 0 150 150" aria-hidden="true">
      <circle cx="75" cy="75" r="64" fill="none" stroke="var(--sun)" stroke-width="7"/>
    </svg>
    <div class="brand">
      <p class="brand-name">maplebrook<small>pediatric dentistry</small></p>
    </div>
    <div class="person">
      <p class="person-name">Corinne Walbeck</p>
      <p class="person-title">DMD</p>
      <p class="address">482 Quarry Lane<br>Suite 517 Ashgrove, PA 17590</p>
      <ul class="contact-list">
        <li>
          <svg viewBox="0 0 10 10" aria-hidden="true"><path d="M2 1l2 2-1 1.2c.6 1.2 1.6 2.2 2.8 2.8L7 6l2 2-1.3 1.3C4.5 9 1 5.5.7 2.3z" fill="var(--sun)"/></svg>
          717.555.0193
        </li>
        <li>
          <svg viewBox="0 0 10 10" aria-hidden="true"><rect x="0.6" y="2" width="8.8" height="6" fill="none" stroke="var(--sun)" stroke-width="1.1"/><path d="M0.6 2l4.4 3.4L9.4 2" fill="none" stroke="var(--sun)" stroke-width="1.1"/></svg>
          hello@maplebrookkids.example
        </li>
        <li>
          <svg viewBox="0 0 10 10" aria-hidden="true"><circle cx="5" cy="5" r="4.3" fill="none" stroke="var(--sun)" stroke-width="1.1"/><path d="M0.7 5h8.6M5 0.7c-2 2.4-2 6.2 0 8.6M5 0.7c2 2.4 2 6.2 0 8.6" fill="none" stroke="var(--sun)" stroke-width="0.9"/></svg>
          www.maplebrookkidsdental.example
        </li>
      </ul>
    </div>
  </section>

</body>
</html>
```